R. Talmont Realty, Inc business card (2 sided), letterhead (1 sided) & #10 envelope (1 sided)

business card of standard size utilizing the attached logo. Side one with logo, Owen Talmont (my name), President / Broker (title), 805-317-2684 (phone), www.rtalmontrealty.example (website), 1726 Harlow Avenue, Suite 4052 San Luis Obiso, CA 93628 (business address) owen.rtalmontrealty@mailbox.example (e-mail address),
Side two - Log

Letterhead and #10 envelope in the same theme
Updates

Project Deadline Extended
Reason: I think a 2 day deadline may be a bit ambitious on my part. I have extended the deadline to 4 days. Thanks!

Industry/Entity Type

Business

```html
<!DOCTYPE html>
<html lang="en">
<head>
<meta charset="utf-8">
<title>R. Talmont Realty, Inc – Business Card</title>
<link href="https://fonts.googleapis.com/css2?family=Open+Sans:wght@400;600;700&display=swap" rel="stylesheet">
<style>
  :root {
    --page: #ece9e4;
    --blue-light: #0d7fb0;
    --blue: #0a6690;
    --blue-dark: #04405c;
    --ink: #2b2b2b;
    --rule: #9a9a9a;
    --white: #ffffff;
  }
  * { margin: 0; padding: 0; box-sizing: border-box; }
  html, body {
    width: 1200px; height: 1183px; overflow: hidden;
    background: var(--page);
    font-family: "Open Sans", Arial, sans-serif;
  }
  .canvas { position: relative; width: 1200px; height: 1183px; }

  .card {
    position: absolute; width: 908px; height: 522px;
    box-shadow: 0 3px 10px rgba(0,0,0,.25);
    overflow: hidden;
  }

  /* Front */
  .card-front { left: 253px; top: 38px; background: var(--white); }
  .front-band {
    position: absolute; left: 0; top: 0; width: 100%; height: 165px;
    background: radial-gradient(ellipse 60% 140% at 40% 0%, var(--blue-light), var(--blue) 55%, var(--blue-dark));
  }
  .front-rule {
    position: absolute; left: 0; top: 165px; width: 100%; height: 3px;
    background: var(--rule);
  }
  .front-logo {
    position: absolute; left: 470px; top: 208px; transform: translateX(-50%);
    display: flex; align-items: center; gap: 14px; white-space: nowrap;
  }
  .logo-mark { width: 22px; height: 22px; }
  .front-logo .logo-mark { background: var(--blue); }
  .front-logo .logo-name { color: var(--blue); font-weight: 600; font-size: 46px; letter-spacing: .5px; }

  .identity { position: absolute; right: 500px; top: 370px; text-align: right; }
  .person-name { color: var(--blue); font-weight: 700; font-size: 33px; line-height: 1.2; }
  .person-title { color: var(--ink); font-size: 25px; margin-top: 4px; letter-spacing: .5px; }

  .divider { position: absolute; left: 413px; top: 355px; width: 2px; height: 118px; background: #c9c9c9; }

  .contacts { position: absolute; left: 432px; top: 355px; list-style: none; }
  .contacts li {
    display: flex; align-items: center; gap: 10px;
    font-size: 22px; color: var(--ink); height: 41px;
  }
  .contacts svg { width: 18px; height: 18px; fill: none; stroke: var(--blue); stroke-width: 2; flex: none; }

  /* Back */
  .card-back {
    left: 29px; top: 609px;
    background: radial-gradient(ellipse 55% 60% at 45% 40%, var(--blue-light), var(--blue) 55%, var(--blue-dark));
  }
  .back-logo {
    position: absolute; left: 0; right: 0; top: 200px;
    display: flex; justify-content: center; align-items: center; gap: 18px;
  }
  .back-logo .logo-mark { width: 28px; height: 28px; background: var(--white); }
  .back-logo .logo-name { color: var(--white); font-weight: 600; font-size: 54px; letter-spacing: .5px; }
  .back-site {
    position: absolute; left: 0; right: 0; top: 428px; text-align: center;
    color: var(--white); font-size: 28px; letter-spacing: 3px;
  }
</style>
</head>
<body>
<main class="canvas">

  <section class="card card-front" aria-label="Business card front">
    <div class="front-band"></div>
    <div class="front-rule"></div>
    <div class="front-logo">
      <span class="logo-mark"></span>
      <span class="logo-name">R. Talmont Realty, Inc</span>
    </div>

    <div class="identity">
      <p class="person-name">Owen Talmont</p>
      <p class="person-title">President / Broker</p>
    </div>
    <div class="divider"></div>
    <ul class="contacts">
      <li>
        <svg viewBox="0 0 20 20"><circle cx="10" cy="10" r="8.5"/><path d="M7 6l2 2-1 1.5c.8 1.5 1.8 2.5 3.5 3.5l1.5-1 2 2-1.5 1.5C10 15 5.5 10.5 5.5 7.5z" fill="currentColor" stroke-width="1"/></svg>
        805-317-2684
      </li>
      <li>
        <svg viewBox="0 0 20 20"><rect x="2" y="5" width="16" height="11" rx="1"/><path d="M2 6l8 6 8-6"/></svg>
        owen.rtalmontrealty@mailbox.example
      </li>
      <li>
        <svg viewBox="0 0 20 20"><circle cx="10" cy="10" r="8"/><ellipse cx="10" cy="10" rx="3.5" ry="8"/><path d="M2 10h16M3.5 6h13M3.5 14h13"/></svg>
        www.rtalmontrealty.example
      </li>
    </ul>
  </section>

  <section class="card card-back" aria-label="Business card back">
    <div class="back-logo">
      <span class="logo-mark"></span>
      <span class="logo-name">R. Talmont Realty, Inc</span>
    </div>
    <p class="back-site">www.rtalmontrealty.example</p>
  </section>

</main>
</body>
</html>
```